Quillbrookes websites redesign

Www.quill-brookes.com needs to be redesigned along with updations. The incremental material will be provided for the updations. We are looking for complete redesign of the pages with the new content. The complete write up will be provided soon

Target Market(s)

Global

Coding

Coded - Design and coding required

Number of Pages Required

5+ page

Requirements
Must have
• A clean and slick design for the Consulting.
Should not have
• Too many pictures which reduces the speed of the site

```html
<!DOCTYPE html>
<html lang="en">
<head>
<meta charset="utf-8">
<title>Quillbrookes – Case Studies</title>
<link href="https://fonts.googleapis.com/css2?family=Mulish:wght@400;600;700&family=Arimo:wght@400;700&display=swap" rel="stylesheet">
<style>
:root{
  --accent:#2fa3cc;
  --ink:#333;
  --muted:#555;
  --rule:#d6d6d6;
  --paper:#fff;
  --footer:#1c1c1c;
  --footer-text:#9a9a9a;
  --footer-rule:#3a3a3a;
  --map:#ece9e2;
  --map-panel:#f7f6f3;
}
*{margin:0;padding:0;box-sizing:border-box}
html,body{width:1200px;height:1200px;overflow:hidden;background:var(--paper)}
body{font-family:"Arimo",Arial,sans-serif;color:var(--ink);position:relative}
.site-header{position:absolute;left:0;top:0;width:1200px;height:65px;border-bottom:1px solid #e6e6e6}
.brand{position:absolute;left:273px;top:18px;display:flex;align-items:center;gap:8px;font-family:"Mulish",sans-serif;font-weight:600;font-size:23px;color:#2b3a55}
.brand-dot{width:26px;height:26px;border-radius:50%;background:#2b3a55}
.main-nav{position:absolute;right:246px;top:0;display:flex;gap:25px;height:65px}
.main-nav a{font-size:11px;color:#666;text-decoration:none;line-height:69px;position:relative}
.main-nav a.is-active{color:var(--accent)}
.main-nav a.is-active::after{content:"";position:absolute;left:0;right:0;bottom:0;height:3px;background:var(--accent)}
.page-title{position:absolute;left:273px;top:114px;font-family:"Mulish",sans-serif;font-weight:400;font-size:18px;color:#444;letter-spacing:.2px}
.page-title strong{font-weight:700;color:#333}
.page-intro{position:absolute;left:273px;top:144px;font-size:9px;color:#444}
.case-card{position:absolute;width:325px;height:220px;border:1px solid var(--rule);background:var(--paper)}
.case-card .icon{position:absolute;left:44px;top:28px}
.case-card h2{position:absolute;left:44px;top:84px;width:250px;font-family:"Mulish",sans-serif;font-weight:600;font-size:10.5px;line-height:15px;color:#444}
.case-card hr{position:absolute;left:44px;top:124px;width:248px;border:0;border-top:1px solid #cfcfcf}
.case-card ul{position:absolute;left:44px;top:143px;list-style:none}
.case-card li{font-size:9px;color:#444;line-height:19.5px}
.map{position:absolute;left:273px;top:685px;width:682px;height:207px;background:var(--map)}
.map-panel{position:absolute;left:31px;top:0;width:200px;height:207px;background:var(--map-panel);padding:63px 0 0 18px}
.map-panel h3{font-size:10px;font-weight:700;color:#333;margin-bottom:14px}
.map-panel p{font-size:8.5px;line-height:15px;color:#333}
.site-footer{position:absolute;left:0;top:928px;width:1200px;height:272px;background:var(--footer);color:var(--footer-text)}
.footer-brand{position:absolute;left:274px;top:48px;display:flex;align-items:center;gap:6px;font-family:"Mulish",sans-serif;font-size:17px;font-weight:600;color:#aaa}
.footer-brand span.mark{width:20px;height:20px;border-radius:50%;background:#aaa}
.footer-address{position:absolute;left:276px;top:90px;font-size:8.5px;line-height:15px}
.footer-contact{position:absolute;left:276px;top:162px;font-size:8.5px;line-height:15.5px}
.footer-contact b{color:var(--accent);font-size:9.5px}
.footer-contact a{color:var(--accent)}
.footer-col{position:absolute;top:52px}
.footer-col h4{font-family:"Mulish",sans-serif;font-weight:600;font-size:10.5px;color:#eee;letter-spacing:.3px}
.footer-col h4::after{content:"";display:block;width:22px;height:1px;background:#888;margin-top:9px}
.signup p{font-size:8.5px;margin-top:12px}
.signup .field{margin-top:11px;width:155px;height:28px;border:1px solid #777;display:flex;align-items:center;justify-content:space-between;padding:0 8px 0 10px;font-size:8.5px;color:#ccc}
.links ul{list-style:none;margin-top:9px}
.links li{font-size:8.5px;line-height:18.5px;color:#aaa}
.links li::before{content:"»";margin-right:7px;color:#777}
.links li.is-current{color:var(--accent);text-decoration:underline}
.social{display:flex;gap:5px;margin-top:13px}
.social span{width:22px;height:22px;border-radius:50%;border:1.5px solid #aaa}
.social span:first-child{border-color:var(--accent)}
.footer-bottom{position:absolute;left:0;top:232px;width:1200px;border-top:1px solid var(--footer-rule);padding:16px 0 0 274px;font-size:8.5px}
</style>
</head>
<body>
<header class="site-header">
  <div class="brand"><span class="brand-dot"></span>Quillbrookes</div>
  <nav class="main-nav">
    <a href="#">home</a><a href="#">founder</a><a href="#">consultancy</a><a href="#">platform</a><a href="#" class="is-active">case studies</a><a href="#">contact</a>
  </nav>
</header>

<h1 class="page-title">QUILLBROOKE <strong>CASE STUDIES</strong></h1>
<p class="page-intro">Some of the deals completed by QCL are summarised below to describe the range of activities undertaken with Corporates</p>

<section class="case-card" style="left:273px;top:182px">
  <svg class="icon" width="38" height="40" viewBox="0 0 38 40" fill="#2fa3cc">
    <rect x="1" y="26" width="9" height="13"/><rect x="13" y="20" width="9" height="19"/><rect x="25" y="14" width="9" height="25"/>
    <path d="M1 22 L13 12 L19 17 L30 6" stroke="#2fa3cc" stroke-width="3" fill="none"/><path d="M26 3 L35 1 L33 10 Z"/>
  </svg>
  <h2>Export Credit Agency backed long term Project financing</h2>
  <hr>
  <ul><li>Case Study 1 - Download as PDF</li></ul>
</section>

<section class="case-card" style="left:629px;top:182px">
  <svg class="icon" width="48" height="40" viewBox="0 0 48 40" fill="#2fa3cc">
    <circle cx="31" cy="6" r="4"/><circle cx="24" cy="14" r="6"/>
    <path d="M1 26 Q8 20 16 24 L26 26 Q30 28 26 30 L16 30 L28 31 L42 24 Q47 23 45 27 L30 38 L12 37 L1 34 Z"/>
  </svg>
  <h2>Introducing Regional/Local banks for International Subsidiary Banking</h2>
  <hr>
  <ul><li>Case Study 1 - Download as PDF</li><li>Case Study 2- Download as PDF</li><li>Case Study 3 - Download as PDF</li></ul>
</section>

<section class="case-card" style="left:273px;top:431px">
  <svg class="icon" width="36" height="38" viewBox="0 0 36 38">
    <circle cx="20" cy="19" r="14" fill="none" stroke="#2fa3cc" stroke-width="3"/>
    <path d="M20 5 V33 M6 19 H34 M9 11 H31 M9 27 H31" stroke="#2fa3cc" stroke-width="2"/>
    <rect x="1" y="3" width="12" height="32" rx="5" fill="#2fa3cc"/>
  </svg>
  <h2>Structured Financing</h2>
  <hr>
  <ul><li>Case Study 1 - Download as PDF</li></ul>
</section>

<section class="case-card" style="left:629px;top:431px">
  <svg class="icon" width="40" height="40" viewBox="0 0 40 40" fill="#2fa3cc">
    <path d="M19 2 A18 18 0 1 0 37 20 L19 20 Z"/><path d="M23 0 L23 16 L38 16 A16 16 0 0 0 23 0 Z" transform="translate(1 -1)" fill="none" stroke="#2fa3cc" stroke-width="3"/>
  </svg>
  <h2>Bank Lines Business</h2>
  <hr>
  <ul><li>Case Study 1 - Download as PDF</li><li>Case Study 2- Download as PDF</li></ul>
</section>

<section class="map" role="img" aria-label="Street map showing the office location">
  <div class="map-panel">
    <h3>Quillbrookes Consultancy Ltd</h3>
    <p>Suite 07, 9th Floor, Harbourline Tower<br>Centre, 28 Marlow Quay Road, Kowloon<br>Hong Kong</p>
  </div>
</section>

<footer class="site-footer">
  <div class="footer-brand"><span class="mark"></span>Quillbrookes</div>
  <p class="footer-address">Quillbrookes Consultancy Ltd<br>Suite 07, 9th Floor, Harbourline Tower<br>Centre, 28 Marlow Quay Road, Kowloon<br>Hong Kong</p>
  <p class="footer-contact">T: <b>852-30417265</b><br>E: <a href="#">query@quill-brookes.com</a></p>

  <div class="footer-col signup" style="left:493px">
    <h4>GET IN TOUCH!</h4>
    <p>Simply Drop Your Mail Here</p>
    <div class="field">Your Email Here
      <svg width="13" height="9" viewBox="0 0 13 9"><rect x=".5" y=".5" width="12" height="8" fill="#2fa3cc"/><path d="M.5 .5 L6.5 5 L12.5 .5" stroke="#1c1c1c" fill="none"/></svg>
    </div>
  </div>

  <div class="footer-col links" style="left:713px">
    <h4>SITE LINKS</h4>
    <ul><li class="is-current">Home</li><li>Founder</li><li>Consultancy</li><li>System</li><li>Case Studies</li><li>Contact</li></ul>
  </div>

  <div class="footer-col" style="left:856px">
    <h4>SOCIAL LINKS</h4>
    <div class="social"><span></span><span></span><span></span><span></span></div>
  </div>

  <div class="footer-bottom">© Quillbrookes Consultancy Limited</div>
</footer>
</body>
</html>
```